Now Leasing Banner

Looking for a banner that says the following information approx 4' x 30'

Now Leasing Maplebrook Terrace 925-318-6042

Target Market(s)

Drive by traffic

Industry/Entity Type

Residential property management

Requirements
Must have
• Clear and readable from a distance

```html
<!DOCTYPE html>
<html lang="en">
<head>
<meta charset="utf-8">
<title>Now Leasing Banner – Maplebrook Terrace</title>
<link rel="stylesheet" href="https://fonts.googleapis.com/css2?family=Anton&family=Archivo+Black&display=swap">
<style>
  :root {
    --banner-green: #4fa300;
    --band-red: #ff0800;
    --text-white: #ffffff;
    --text-outline: #111111;
    --page-bg: #ffffff;
  }
  html, body {
    margin: 0;
    padding: 0;
    width: 1200px;
    height: 1200px;
    overflow: hidden;
    background: var(--page-bg);
  }
  .canvas {
    position: relative;
    width: 1200px;
    height: 1200px;
  }
  .feather-banner {
    position: absolute;
    left: 526px;
    top: 50px;
    width: 147px;
    height: 1100px;
    display: block;
  }
  .banner-field { fill: var(--banner-green); }
  .phone-band { fill: var(--band-red); }
  .headline,
  .phone-number {
    font-family: "Anton", "Impact", sans-serif;
    fill: var(--text-white);
    stroke: var(--text-outline);
    paint-order: stroke fill;
    stroke-linejoin: round;
  }
  .headline {
    font-size: 90px;
    stroke-width: 3px;
    filter: drop-shadow(-3px 3px 2px rgba(0,0,0,0.75));
  }
  .now-word {
    font-family: "Archivo Black", "Arial Black", sans-serif;
    font-size: 38px;
    fill: var(--text-white);
    stroke: var(--text-outline);
    stroke-width: 2.5px;
    paint-order: stroke fill;
    stroke-linejoin: round;
    filter: drop-shadow(-2px 2px 1.5px rgba(0,0,0,0.7));
  }
  .phone-number {
    font-size: 36px;
    stroke-width: 2px;
  }
</style>
</head>
<body>
<main class="canvas">
  <svg class="feather-banner" viewBox="0 0 147 1100" xmlns="http://www.w3.org/2000/svg" aria-label="Now Leasing Maplebrook Terrace banner">
    <rect class="banner-field" x="0" y="0" width="147" height="1100"/>
    <rect class="phone-band" x="0" y="978" width="147" height="74"/>

    <text class="headline" transform="translate(111,868) rotate(-90)" x="0" y="0"
          textLength="814" lengthAdjust="spacingAndGlyphs">LEASING MAPLEBROOK TERRACE</text>

    <text class="now-word" transform="translate(75,940) rotate(-20)" x="0" y="0"
          text-anchor="middle" textLength="104" lengthAdjust="spacingAndGlyphs">NOW</text>

    <text class="phone-number" x="73.5" y="1030" text-anchor="middle"
          textLength="114" lengthAdjust="spacingAndGlyphs">925-318-6042</text>
  </svg>
</main>
</body>
</html>
```